Harbourline Electrical Solutions

On one side. LOGO (underneath:) Commercial Industrial Residential

- NAME & CONTACT DETAILS

Marcus T. Hollings
Project Manager

(Cell icon) (441) 555-0187
(Email icon) hlelectricalsolutions@mailvento.com
(Facebook & Instagram icons )@hlelectricalsolutions

Other side: LOGO - underneath ELECTRICAL CONSTRUCTION & MAINTENANCE . LED LIGHTING & AUTOMATION . LIFE SAFETY SYSTEMS (FIRE ALARM / SECURITY) . DATA & COMMUNICATION

```html
<!DOCTYPE html>
<html lang="en">
<head>
<meta charset="utf-8">
<title>Harbourline Electrical Solutions – Business Card</title>
<link rel="stylesheet" href="https://fonts.googleapis.com/css2?family=Montserrat:wght@500;600&family=Work+Sans:wght@400;500&display=swap">
<style>
  :root {
    --stage: #3b3b3d;
    --card: #1d1d1f;
    --ink: #ffffff;
    --ink-soft: #d9d9d9;
    --rule: #bdbdbd;
  }
  * { box-sizing: border-box; margin: 0; padding: 0; }
  html, body { width: 1200px; height: 900px; overflow: hidden; background: var(--stage); }
  .canvas {
    width: 1200px; height: 900px;
    display: flex; flex-direction: column; align-items: center;
    justify-content: center; gap: 40px;
  }
  .card {
    position: relative;
    width: 700px; height: 400px;
    background: var(--card);
    border-radius: 22px;
    color: var(--ink);
    overflow: hidden;
    box-shadow: 0 10px 30px rgba(0,0,0,.35);
  }

  /* Services side */
  .services-side .brand {
    position: absolute; top: 56px; left: 230px;
    display: flex; align-items: center; gap: 22px;
  }
  .brand-mark {
    width: 46px; height: 46px; background: var(--ink-soft); border-radius: 4px;
  }
  .brand-rule { width: 1.5px; height: 92px; background: var(--rule); }
  .brand-name {
    font-family: "Montserrat", sans-serif; font-weight: 500;
    font-size: 25px; letter-spacing: 3.5px; line-height: 1.08;
    text-transform: uppercase; color: var(--ink-soft);
  }
  .service-list {
    position: absolute; top: 215px; left: 118px;
    list-style: none;
    font-family: "Montserrat", sans-serif; font-weight: 600;
    font-size: 17px; letter-spacing: 1.6px; line-height: 1.5;
    text-transform: uppercase;
  }
  .service-list li { position: relative; padding-left: 22px; }
  .service-list li::before {
    content: ""; position: absolute; left: 0; top: 10px;
    width: 7px; height: 7px; border-radius: 50%; background: var(--ink);
  }

  /* Contact side */
  .contact-side .brand-block {
    position: absolute; top: 118px; left: 56px; width: 212px;
  }
  .brand-block-name {
    font-family: "Montserrat", sans-serif; font-weight: 600;
    font-size: 26px; line-height: 1.12; letter-spacing: .5px;
    text-transform: uppercase;
  }
  .brand-tagline {
    margin-top: 10px;
    font-family: "Work Sans", sans-serif; font-size: 11px;
    letter-spacing: .4px; color: var(--ink-soft); white-space: nowrap;
  }
  .contact-side .divider {
    position: absolute; top: 100px; left: 286px;
    width: 1.5px; height: 150px; background: var(--rule);
  }
  .contact {
    position: absolute; top: 106px; left: 314px; right: 24px;
    font-family: "Work Sans", sans-serif;
  }
  .person-name {
    font-family: "Montserrat", sans-serif; font-weight: 600;
    font-size: 22px; letter-spacing: 1.6px; text-transform: uppercase;
    white-space: nowrap;
  }
  .person-role { font-size: 17px; letter-spacing: .6px; margin: 2px 0 14px; }
  .contact-line {
    display: flex; align-items: center; gap: 10px;
    font-size: 16px; letter-spacing: .3px; line-height: 1.7;
    white-space: nowrap;
  }
  .contact-line svg { width: 16px; height: 16px; flex: none; }
  .social {
    position: absolute; bottom: 40px; left: 0; right: 0;
    display: flex; justify-content: center; align-items: center; gap: 12px;
    font-family: "Work Sans", sans-serif; font-size: 18px; letter-spacing: .5px;
  }
  .social-square { width: 18px; height: 18px; background: var(--ink); border-radius: 3px; }
</style>
</head>
<body>
<main class="canvas">

  <section class="card services-side" aria-label="Card back – services">
    <div class="brand">
      <span class="brand-mark" aria-hidden="true"></span>
      <span class="brand-rule" aria-hidden="true"></span>
      <p class="brand-name">Harbourline<br>Electrical<br>Solutions</p>
    </div>
    <ul class="service-list">
      <li>Data &amp; Communication</li>
      <li>LED Lighting &amp; Automation</li>
      <li>Electrical Construction &amp; Maintenance</li>
      <li>Life Safety Systems (Fire Alarm / Security)</li>
    </ul>
  </section>

  <section class="card contact-side" aria-label="Card front – contact">
    <div class="brand-block">
      <p class="brand-block-name">Harbourline<br>Electrical<br>Solutions</p>
      <p class="brand-tagline">Commercial · Industrial · Residential</p>
    </div>
    <span class="divider" aria-hidden="true"></span>
    <div class="contact">
      <p class="person-name">Marcus T. Hollings</p>
      <p class="person-role">Project Manager</p>
      <p class="contact-line">
        <svg viewBox="0 0 24 24" aria-hidden="true"><path d="M6.6 10.8a15 15 0 0 0 6.6 6.6l2.2-2.2a1 1 0 0 1 1-.25 11.4 11.4 0 0 0 3.6.57 1 1 0 0 1 1 1V20a1 1 0 0 1-1 1A17 17 0 0 1 3 4a1 1 0 0 1 1-1h3.5a1 1 0 0 1 1 1c0 1.25.2 2.45.57 3.6a1 1 0 0 1-.25 1z" fill="none" stroke="#fff" stroke-width="1.8"/></svg>
        (441) 555-0187
      </p>
      <p class="contact-line">
        <svg viewBox="0 0 24 24" aria-hidden="true"><rect x="3" y="5" width="18" height="14" rx="1.5" fill="none" stroke="#fff" stroke-width="1.8"/><path d="M3.5 6l8.5 7 8.5-7" fill="none" stroke="#fff" stroke-width="1.8"/></svg>
        hlelectricalsolutions@mailvento.com
      </p>
    </div>
    <p class="social">
      <span class="social-square" aria-hidden="true"></span>
      @hlelectricalsolutions
    </p>
  </section>

</main>
</body>
</html>
```